Business card for my new company (Accounting firm)

I need a business card for my new business Brightwell Advisory and Ledger SA. Our services are accounting, tax, audit and financial management. Our customers are small companies, start-ups and new companies. The final design has to show financial security, trust and growth. Please find our logo attached to the business card. Text for the business card: Brightwell Advisory and Ledger SA Tomas Varenholt Director and Founder Certified Accountant Tel. 022 418 57 34 tv@clairevalconseil.ch www.clairevalconseil.ch Rue des Vergières 27 1201 Geneva
Target Market(s)
Our customers are small companies, start-ups and new companies.
Industry/Entity Type
Finance And Accounting
Contact Information for Business Card
Claireval Conseil et Comptes SA
Tomas Varenholt
Directeur et Fondateur
Expert-comptable diplômé
Tél. 022 418 57 34
tv@clairevalconseil.ch
www.clairevalconseil.ch
Rue des Vergières 27
1201 Genève

```html
<!DOCTYPE html>
<html lang="fr">
<head>
<meta charset="utf-8">
<title>Claireval Conseil et Comptes SA – Carte de visite</title>
<link rel="stylesheet" href="https://fonts.googleapis.com/css2?family=Saira:wght@400;500;700&display=swap">
<style>
  :root {
    --backdrop: #3b3c3e;
    --card-white: #ffffff;
    --card-dark-top: #4a4b4d;
    --card-dark-bottom: #2f3032;
    --brand-blue: #2fa9e0;
    --brand-blue-deep: #1f6fae;
    --ink: #4d4e50;
    --ink-soft: #6a6b6d;
    --rule: #7a7b7d;
    --on-dark: #ffffff;
  }
  * { box-sizing: border-box; margin: 0; padding: 0; }
  html, body {
    width: 1200px; height: 1000px; overflow: hidden;
    background: var(--backdrop);
    font-family: "Saira", "Helvetica Neue", Arial, sans-serif;
  }
  .stage {
    width: 1200px; height: 1000px;
    display: flex; flex-direction: column;
    align-items: center; justify-content: center; gap: 40px;
  }
  .card {
    width: 760px; height: 434px;
    border-radius: 4px;
    box-shadow: 0 14px 30px rgba(0,0,0,.35);
    position: relative; overflow: hidden;
  }

  /* Back */
  .card--back {
    background: linear-gradient(135deg, var(--card-dark-top), var(--card-dark-bottom));
    display: flex; align-items: center; justify-content: flex-end;
    padding-right: 90px;
  }
  .brand {
    display: flex; align-items: center; gap: 18px;
  }
  .brand__mark {
    width: 46px; height: 46px; flex: none;
  }
  .brand__name {
    font-weight: 500; font-size: 34px; line-height: 1.05;
    letter-spacing: .04em; text-transform: uppercase;
  }
  .card--back .brand__mark { background: var(--on-dark); }
  .card--back .brand__name { color: var(--on-dark); }

  /* Front */
  .card--front {
    background: var(--card-white);
    display: grid;
    grid-template-columns: 392px 1px 1fr;
    align-items: center;
  }
  .card--front .brand { justify-content: center; }
  .card--front .brand__mark { background: var(--brand-blue); }
  .card--front .brand__name { color: var(--ink); font-size: 30px; }
  .divider {
    width: 1px; height: 240px; background: var(--rule);
  }
  .contact {
    padding-left: 50px;
    color: var(--ink-soft);
    font-size: 17px; line-height: 1.35;
  }
  .contact__name {
    color: var(--brand-blue); font-weight: 700; font-size: 22px;
  }
  .contact__group + .contact__group { margin-top: 14px; }
</style>
</head>
<body>
<main class="stage">
  <section class="card card--back" aria-label="Verso de la carte">
    <div class="brand">
      <span class="brand__mark"></span>
      <p class="brand__name">Claireval<br>Conseil et Comptes</p>
    </div>
  </section>

  <section class="card card--front" aria-label="Recto de la carte">
    <div class="brand">
      <span class="brand__mark"></span>
      <p class="brand__name">Claireval<br>Conseil et Comptes</p>
    </div>
    <span class="divider"></span>
    <div class="contact">
      <div class="contact__group">
        <p class="contact__name">Tomas Varenholt</p>
        <p>Directeur et Fondateur</p>
        <p>Expert-comptable diplômé</p>
      </div>
      <div class="contact__group">
        <p>022 418 57 34</p>
        <p>tv@clairevalconseil.ch</p>
        <p>www.clairevalconseil.ch</p>
      </div>
      <div class="contact__group">
        <p>Rue des Vergières 27</p>
        <p>1201 Genève</p>
      </div>
    </div>
  </section>
</main>
</body>
</html>
```